holloway paving service

Needs to have phone number 0418259730 and email markholloway@brightmail.com.au.
ABN 62318470915
name mark holloway

For all your concreting solutions
Excavation
Exposed & colour concrete
House & shed slabs
Driveways
Landing & steps

Contact Information for Business Card

ph 0418259730
email markholloway@brightmail.com.au.
ABN 62318470915
name mark holloway

```html
<!DOCTYPE html>
<html lang="en">
<head>
<meta charset="utf-8">
<title>Holloway Paving Service — Business Card</title>
<link href="https://fonts.googleapis.com/css2?family=Roboto:wght@300;400;500&family=Roboto+Condensed:wght@400;500&display=swap" rel="stylesheet">
<style>
  :root {
    --bg: #e9e6e1;
    --card-white: #ffffff;
    --card-grey: #58595b;
    --slate: #6d6e70;
    --orange: #ea6a1f;
    --text-dark: #58595b;
    --text-light: #f2f2f2;
    --faint: rgba(255,255,255,0.07);
  }
  * { box-sizing: border-box; margin: 0; padding: 0; }
  html, body { width: 1200px; height: 886px; overflow: hidden; }
  body {
    background: var(--bg);
    font-family: "Roboto", Arial, sans-serif;
    display: flex; align-items: center; justify-content: center; gap: 60px;
  }
  .card {
    position: relative; width: 525px; height: 300px;
    box-shadow: 0 6px 20px rgba(0,0,0,0.18); overflow: hidden;
  }
  /* Front */
  .card--front { background: var(--card-white); color: var(--text-dark); }
  .brand {
    position: absolute; left: 32px; top: 96px;
    display: flex; align-items: center; gap: 14px;
  }
  .brand__mark { width: 34px; height: 34px; background: var(--orange); }
  .brand__text {
    border-left: 1px solid var(--orange); padding-left: 12px;
    font-family: "Roboto Condensed", Arial, sans-serif; line-height: 1.1;
  }
  .brand__name { color: var(--orange); font-size: 15px; font-weight: 500; text-transform: uppercase; }
  .brand__sub { font-size: 13px; letter-spacing: 2px; text-transform: uppercase; color: var(--text-dark); }
  .brand__phone { font-size: 12px; color: var(--orange); }
  .person { position: absolute; left: 280px; top: 58px; }
  .person__name {
    font-family: "Roboto Condensed", Arial, sans-serif;
    color: var(--orange); font-size: 22px; font-weight: 500; text-transform: uppercase; margin-bottom: 10px;
  }
  .person__line { display: flex; align-items: center; gap: 8px; font-size: 12.5px; margin-bottom: 6px; font-weight: 300; }
  .person__line svg { width: 11px; height: 11px; fill: var(--orange); flex: none; }
  .band {
    position: absolute; left: 0; bottom: 26px; width: 100%; height: 36px; display: flex;
  }
  .band__web {
    flex: 1; background: var(--orange); color: #fff; font-size: 13px; letter-spacing: 5px;
    display: flex; align-items: center; justify-content: center;
  }
  .band__end { width: 92px; background: var(--slate); display: flex; align-items: center; justify-content: center; }
  .band__end span { width: 14px; height: 14px; background: #fff; }
  /* Back */
  .card--back { background: var(--card-grey); color: var(--text-light); }
  .back__deco { position: absolute; left: 150px; top: -20px; width: 190px; height: 190px; background: var(--faint); }
  .back__brand { position: absolute; left: 30px; bottom: 40px; font-family: "Roboto Condensed", Arial, sans-serif; line-height: 1.15; }
  .back__brand .brand__name { font-size: 18px; border-bottom: 1px solid var(--text-light); padding-bottom: 2px; }
  .back__brand .brand__sub { color: var(--text-light); font-size: 14px; letter-spacing: 3px; }
  .back__brand .brand__phone { font-size: 13px; }
  .back__web { font-family: "Roboto", Arial, sans-serif; font-size: 11px; letter-spacing: 4px; margin-top: 4px; }
  .services { position: absolute; right: 30px; top: 140px; list-style: none; text-align: right; }
  .services li { font-size: 13px; font-weight: 300; margin-bottom: 3px; }
  .services li::after {
    content: ""; display: inline-block; width: 5px; height: 5px; border-radius: 50%;
    background: var(--orange); margin-left: 8px; vertical-align: middle;
  }
</style>
</head>
<body>
  <section class="card card--front">
    <div class="brand">
      <span class="brand__mark"></span>
      <div class="brand__text">
        <div class="brand__name">Holloway Paving Service</div>
        <div class="brand__sub">Solutions</div>
        <div class="brand__phone">0418259730</div>
      </div>
    </div>
    <div class="person">
      <div class="person__name">Mark Holloway</div>
      <div class="person__line">
        <svg viewBox="0 0 24 24"><path d="M6.6 10.8a15 15 0 0 0 6.6 6.6l2.2-2.2a1 1 0 0 1 1-.25 11.4 11.4 0 0 0 3.6.57 1 1 0 0 1 1 1V20a1 1 0 0 1-1 1A17 17 0 0 1 3 4a1 1 0 0 1 1-1h3.5a1 1 0 0 1 1 1c0 1.25.2 2.45.57 3.6a1 1 0 0 1-.25 1z"/></svg>
        0418259730
      </div>
      <div class="person__line">
        <svg viewBox="0 0 24 24"><path d="M2 5h20v14H2zm2 2v.5l8 5 8-5V7l-8 5z"/></svg>
        markholloway@brightmail.com.au
      </div>
      <div class="person__line" style="padding-left:19px">ABN 62318470915</div>
    </div>
    <div class="band">
      <div class="band__web">www.hollowaypaving.com.au</div>
      <div class="band__end"><span></span></div>
    </div>
  </section>

  <section class="card card--back">
    <div class="back__deco"></div>
    <ul class="services">
      <li>Excavation</li>
      <li>Exposed &amp; colour concrete</li>
      <li>House &amp; shed slabs</li>
      <li>Driveways</li>
      <li>Landing &amp; steps</li>
    </ul>
    <div class="back__brand">
      <div class="brand__name">Holloway Paving Service</div>
      <div class="brand__sub">Solutions</div>
      <div class="brand__phone">0418259730</div>
      <div class="back__web">www.hollowaypaving.com.au</div>
    </div>
  </section>
</body>
</html>
```